Veltrano.co - Polar Expeditions Specialists

We need a modern, visually striking business card for Veltrano.co, a company specialized in selling expedition cruises to the most remote regions on Earth, with a focus on the Arctic and Antarctica. The design should instantly communicate that the cardholder is an expert in polar travel. Use clean, premium aesthetics with cool tones like icy blue and white, possibly incorporating polar imagery (ice, glaciers, penguins, etc.)

Attached the logo

Contact Information for Business Card

Feels high-end and trustworthy.. Visually memorable — encourages people to keep it

Colors
0054AA
0677BA
7BADD7
CADEEF
E8F1F8

Requirements
Must have
• ice, glaciers, penguins, montains
Nice to have
• modern, transparente,

```html
<!DOCTYPE html>
<html lang="en">
<head>
<meta charset="utf-8">
<title>Veltrano.co – Business Card</title>
<link href="https://fonts.googleapis.com/css2?family=Arimo:wght@400;700&family=Poppins:wght@600;700&display=swap" rel="stylesheet">
<style>
  :root {
    --backdrop: #e4e4e4;
    --card-white: #f4f4f6;
    --brand-blue: #2e6aae;
    --ink: #1f1f1f;
    --muted: #555555;
    --rule: #222222;
    --band-line: #5a6470;
    --pattern-deep: #1e3f8c;
    --pattern-mid: #2e6aae;
    --pattern-ice: #5cd0ef;
  }
  * { margin: 0; padding: 0; box-sizing: border-box; }
  html, body { width: 1200px; height: 1040px; overflow: hidden; }
  body { background: var(--backdrop); position: relative; font-family: "Arimo", Arial, sans-serif; }

  .card { position: absolute; border-radius: 16px; overflow: hidden; box-shadow: 0 3px 6px rgba(0,0,0,.18); }

  .card-front { left: 285px; top: 130px; width: 640px; height: 366px; background: var(--card-white); }

  .brand { position: absolute; right: 42px; top: 112px; text-align: center; font-family: "Poppins", Arial, sans-serif; color: var(--brand-blue); }
  .brand-name { font-size: 35px; font-weight: 700; line-height: 1; letter-spacing: -0.3px; }
  .brand-tagline { font-size: 11px; font-weight: 600; margin-top: 8px; }

  .holder { position: absolute; left: 46px; top: 204px; }
  .holder-name { font-size: 24px; font-weight: 700; color: var(--brand-blue); line-height: 1.1; }
  .holder-title { font-size: 16px; color: var(--muted); margin-top: 2px; }

  .divider { position: absolute; left: 46px; top: 254px; width: 552px; height: 1px; background: var(--rule); }

  .contacts { position: absolute; left: 46px; top: 268px; list-style: none; font-size: 15.5px; color: var(--ink); }
  .contacts li { display: flex; align-items: center; height: 20px; }
  .contacts svg { width: 13px; height: 13px; margin-right: 7px; fill: var(--brand-blue); }

  .address { position: absolute; right: 42px; top: 270px; text-align: right; font-size: 15.5px; line-height: 20px; color: var(--ink); font-style: normal; }

  .band-line { position: absolute; left: 0; top: 345px; width: 100%; height: 3px; background: var(--band-line); }
  .band { position: absolute; left: 0; top: 350px; width: 100%; height: 16px; background: var(--brand-blue); }

  .card-back { left: 285px; top: 567px; width: 646px; height: 369px; background: var(--pattern-mid); }
  .card-back .pattern { width: 100%; height: 100%;
    background: linear-gradient(90deg, var(--pattern-deep) 0%, var(--pattern-mid) 45%, #4aa8dc 72%, var(--pattern-ice) 100%); opacity: .9; }
</style>
</head>
<body>
  <section class="card card-front" aria-label="Business card front">
    <div class="brand">
      <div class="brand-name">Veltrano.co</div>
      <div class="brand-tagline">Polar Expeditions Specialists</div>
    </div>

    <div class="holder">
      <div class="holder-name">Marcus Hale</div>
      <div class="holder-title">President</div>
    </div>

    <div class="divider"></div>

    <ul class="contacts">
      <li><svg viewBox="0 0 24 24"><path d="M6.6 10.8a15.1 15.1 0 0 0 6.6 6.6l2.2-2.2c.3-.3.7-.4 1-.2 1.1.4 2.3.6 3.6.6.6 0 1 .4 1 1V20c0 .6-.4 1-1 1C10.6 21 3 13.4 3 4c0-.6.4-1 1-1h3.5c.6 0 1 .4 1 1 0 1.3.2 2.5.6 3.6.1.3 0 .7-.2 1L6.6 10.8z"/></svg>(555) 0142-7781</li>
      <li><svg viewBox="0 0 24 24"><path d="M2 5h20v14H2z M3.5 6.5 12 13l8.5-6.5" fill="none" stroke="#2e6aae" stroke-width="2"/></svg>name@veltrano.com</li>
      <li><svg viewBox="0 0 24 24"><circle cx="12" cy="12" r="10"/><path d="M7 7c2 1 2 3 4 3s1 3 3 3-1 4 1 5M15 4c0 2 3 2 3 4" fill="none" stroke="#f4f4f6" stroke-width="1.6"/></svg>www.veltrano.com</li>
    </ul>

    <address class="address">4172 Harbor Crest Lane<br>Glenmoor, NY 10290</address>

    <div class="band-line"></div>
    <div class="band"></div>
  </section>

  <section class="card card-back" aria-label="Business card back">
    <div class="pattern" role="img" aria-label="Repeating brand-mark pattern fading from deep navy to icy cyan across the card"></div>
  </section>
</body>
</html>
```